Heron Loan Partners Business Card

We need a business card design for our mortgage servicing company. In addition to servicing the loans of homeowners, we help homeowners with purchasing their homes and any mortgage refinancing. We would like to see designs that use the colors in the logo attached below (gold-ish yellow and navy blue), and any other design you deem fit! The design should communicate a simpler life with smart mortgages provided by Heron.

```html
<!DOCTYPE html>
<html lang="en">
<head>
<meta charset="utf-8">
<title>Heron Loan Partners – Business Card</title>
<link href="https://fonts.googleapis.com/css2?family=Poppins:wght@400;600;700&display=swap" rel="stylesheet">
<style>
  :root {
    --navy: #231f52;
    --navy-soft: #2b2760;
    --gold: #e0b43a;
    --paper: #ffffff;
    --ink: #231f52;
    --text: #2a2a2a;
  }
  * { box-sizing: border-box; margin: 0; padding: 0; }
  html, body { width: 876px; height: 1200px; overflow: hidden; background: var(--paper); }
  body { font-family: 'Poppins', sans-serif; position: relative; }

  .card {
    position: absolute;
    top: 267px;
    width: 380px;
    height: 665px;
    overflow: hidden;
    box-shadow: 0 6px 18px rgba(0,0,0,0.22);
  }
  .card--front { left: 38px; background: var(--navy); }
  .card--back { left: 458px; background: var(--paper); }

  .front-art { position: absolute; inset: 0; width: 100%; height: 100%; }

  .wordmark {
    position: absolute;
    left: 0; right: 0;
    text-align: center;
    color: var(--gold);
    font-weight: 700;
    line-height: 1.05;
    letter-spacing: 0.5px;
  }
  .wordmark .line-main { display: block; font-size: 44px; }
  .wordmark .line-sub { display: block; font-size: 17px; letter-spacing: 3px; }
  .card--front .wordmark { top: 290px; }
  .card--back .wordmark { top: 140px; }

  .band {
    position: absolute; left: 0; right: 0;
    background: linear-gradient(100deg, var(--navy) 0%, var(--navy-soft) 55%, var(--navy) 100%);
  }
  .band--top { top: 0; height: 61px; }
  .band--bottom { bottom: 0; height: 68px; }

  .person { position: absolute; top: 243px; left: 0; right: 0; text-align: center; }
  .person__name { color: var(--ink); font-weight: 700; font-size: 23px; letter-spacing: 0.3px; }
  .person__title { color: var(--text); font-weight: 400; font-size: 17px; margin-top: -3px; }

  .contact { position: absolute; left: 0; right: 0; text-align: center; color: var(--text); font-size: 16px; line-height: 1.25; }
  .icon {
    position: absolute; left: 50%; margin-left: -10px;
    width: 20px; height: 20px; border-radius: 4px; background: var(--gold);
    display: flex; align-items: center; justify-content: center;
  }
  .icon svg { width: 12px; height: 12px; }
</style>
</head>
<body>

<section class="card card--front" aria-label="Card front">
  <svg class="front-art" viewBox="0 0 380 665" preserveAspectRatio="none">
    <rect width="380" height="665" fill="var(--navy)" role="img" aria-label="Faint line illustration of fish on navy"/>
    <polygon points="0,126 380,226 380,538 0,432" fill="var(--paper)"/>
    <line x1="0" y1="126" x2="380" y2="226" stroke="var(--gold)" stroke-width="5"/>
    <line x1="0" y1="432" x2="380" y2="538" stroke="var(--gold)" stroke-width="5"/>
  </svg>
  <div class="wordmark">
    <span class="line-main">Heron</span>
    <span class="line-sub">LOAN PARTNERS</span>
  </div>
</section>

<section class="card card--back" aria-label="Card back">
  <div class="band band--top" role="img" aria-label="Navy band with faint fish line illustration"></div>

  <div class="wordmark">
    <span class="line-main">Heron</span>
    <span class="line-sub">LOAN PARTNERS</span>
  </div>

  <div class="person">
    <p class="person__name">DANIEL R. WHITFORD</p>
    <p class="person__title">CEO/Founder</p>
  </div>

  <span class="icon" style="top:314px">
    <svg viewBox="0 0 24 24"><path fill="var(--navy)" d="M6.6 10.8a15.1 15.1 0 0 0 6.6 6.6l2.2-2.2c.3-.3.7-.4 1-.2 1.1.4 2.3.6 3.6.6.6 0 1 .4 1 1V20c0 .6-.4 1-1 1A17 17 0 0 1 3 4c0-.6.4-1 1-1h3.5c.6 0 1 .4 1 1 0 1.2.2 2.4.6 3.6.1.3 0 .7-.2 1z"/></svg>
  </span>
  <p class="contact" style="top:342px">(888)-555-0142</p>

  <span class="icon" style="top:371px">
    <svg viewBox="0 0 24 24"><path fill="var(--navy)" d="M12 2a7 7 0 0 0-7 7c0 5.2 7 13 7 13s7-7.8 7-13a7 7 0 0 0-7-7zm0 9.5A2.5 2.5 0 1 1 12 6.5a2.5 2.5 0 0 1 0 5z"/></svg>
  </span>
  <p class="contact" style="top:396px">218 Bayview Ave S, Lake<br>Harbor, OR 97455</p>

  <span class="icon" style="top:451px">
    <svg viewBox="0 0 24 24"><path fill="var(--navy)" d="M3 5h18v14H3z"/><path fill="none" stroke="var(--gold)" stroke-width="2" d="M3 6l9 7 9-7"/></svg>
  </span>
  <p class="contact" style="top:479px">info@heronloans.com</p>

  <span class="icon" style="top:509px">
    <svg viewBox="0 0 24 24"><circle cx="12" cy="12" r="9" fill="none" stroke="var(--navy)" stroke-width="2"/><ellipse cx="12" cy="12" rx="4" ry="9" fill="none" stroke="var(--navy)" stroke-width="2"/><line x1="3" y1="12" x2="21" y2="12" stroke="var(--navy)" stroke-width="2"/></svg>
  </span>
  <p class="contact" style="top:536px">www.heronloans.com</p>

  <div class="band band--bottom" role="img" aria-label="Navy band with faint fish line illustration"></div>
</section>

</body>
</html>
```